Dentistry Office

We want a new design for a Dentist's office website.

The theme is: "We provide high quality, state-of-the-art, dental care in a comfortable, caring environment."

The site currently has a menu on the left of the page with about 40 items on it. There is a great deal of textual content on each page, plus several illustrations.

We want to do this using CSS, so we need specifications in the CSS for all possible elements. The CSS needs to be named in a logical manner for easy use.

Every dentist on the planet seems to use lots of Flash. We don't want to because it is so distracting. We are looking for an elegant solution targeting 24-55 age group, but not excluding anyone.

The following (from another dentist's site) can give you a taste of what we want to communicate on the site:

"After 20 years of teaching dentists how to refine their technique and many years of writing textbooks, I currently devote my time to my office and the hands-on practice of dentistry. I'd like to welcome you personally to my dental practice, and I invite you to meet my highly experienced team of professionals.

"We have offered complete dental care of the highest quality since 1978. We provide Preventive Services, Tooth Whitening and Cosmetic Dentistry for a beautiful smile, Endodontics (root canal treatment) to treat painful teeth, Sedation Dentistry so you can relax, and Dental Implants to restore what is missing. We offer total care.

"Our approach to your health is simple: We use our education, experience and dedication to provide every patient with superior dental care.

"This passion for excellence is not just a goal, but a standard every member of our team holds.

"We also pride ourselves with our state of the art procedures, training and technology. This includes creating a beautiful smile using techniques that preserve as much of the original tooth as possible.

"Our abilities are renowned throughout the dental profession and I hope if you have any questions you will contact us by an e-mail note, by phone or just by dropping by."

Keep in mind the screen shape and dimensions. Your design needs to work in the normal screen proportions, regardless of how it looks when you post it here. Scrolling is OK, but the first impression needs to work.
Updates

Keep in mind that there will be about 250 words, or more, on each page.

Competitors web sites:

http://www.brindlecovedentist.example/

http://www.brindlecovedentalcare.example/

http://www.grinsbymarlowvaledental.example/

http://www.tenbyfamilydentalcare.example/

http://www.quelmardental.example/

http://www.dovrinadental.example/

We need to compete with these.

Target Market(s)

Generally adults seeking the most experienced and comfortable-to-be-with dentist.

Industry/Entity Type

Training

Requirements
Must have
• Must stand apart from other dentists.
• Must be elegant.
• Must have a horizontal menu structure across all columns, NOT a vertical that requires scrolling, no popout, pop down, etc. menus.
• We are looking for something special.
• Do not waste your time or ours putting up templates and things you have used before.
• Personally, I do not see how someone outside the US can understand the northern California dental market. But you are welcome to try.
Should not have
• Flash or graphics that move
• The look of a template
• Folksy fonts
• Looks like you used it 20 times before

```html
<!DOCTYPE html>
<html lang="en">
<head>
<meta charset="utf-8">
<title>Larkmoor Dentist — Corwin Hale, DDS, FAGD</title>
<link href="https://fonts.googleapis.com/css2?family=Arimo:wght@400;700&family=Fira+Sans:wght@400;500&display=swap" rel="stylesheet">
<style>
:root{
  --brick:#a8300e;
  --brick-dark:#6e1d08;
  --brick-deep:#5a1606;
  --cream:#f5f2ea;
  --sand:#e9e1c9;
  --sand-line:#d5c9a6;
  --ink:#3b3b3b;
  --slate:#3f4f55;
  --white:#ffffff;
}
*{margin:0;padding:0;box-sizing:border-box}
html,body{width:886px;height:1200px;overflow:hidden;background:var(--cream)}
body{font-family:"Arimo",Arial,sans-serif;color:var(--ink);position:relative}
a{color:inherit;text-decoration:none}

.site-header{position:absolute;left:0;top:0;width:886px;height:252px;background:var(--white)}
.header-band{position:absolute;left:0;top:11px;width:886px;height:241px;
  background:radial-gradient(ellipse at 30% 40%,#b8401a 0%,var(--brick) 45%,#8c260b 100%)}
.call-tab{position:absolute;left:72px;top:0;width:350px;height:34px;background:linear-gradient(#ffffff,#e6e6e6);
  clip-path:polygon(0 0,100% 0,93% 100%,6% 100%);font-family:"Fira Sans",sans-serif;font-size:15px;color:#4a4a4a;
  padding:10px 0 0 29px;letter-spacing:.6px}
.site-title{position:absolute;left:83px;top:102px;font-family:"Fira Sans",sans-serif;font-weight:500;font-size:32px;
  line-height:36px;color:var(--white);letter-spacing:.9px;text-shadow:0 1px 2px rgba(0,0,0,.3)}
.hero-photo{position:absolute;left:443px;top:11px;width:400px;height:241px;
  background:radial-gradient(ellipse at 55% 45%,#f2d9c3 0%,#e6c09d 30%,#b8552b 70%,rgba(168,48,14,0) 100%)}

.main-nav{position:absolute;left:0;top:252px;width:886px;height:35px;background:linear-gradient(var(--brick-deep),#7a200a)}
.main-nav ul{list-style:none;position:absolute;left:72px;top:0;display:flex;height:35px}
.main-nav li{font-size:11.5px;font-weight:700;color:var(--white);height:35px;line-height:35px;
  border-right:1px dotted rgba(255,255,255,.2);letter-spacing:.6px;text-align:center;white-space:nowrap}
.main-nav li.is-current{background:var(--cream);color:var(--brick-dark)}
.main-nav li:last-child{border-right:0}

.topic-index{position:absolute;left:73px;top:310px;width:175px;height:802px;background:var(--sand)}
.topic-head{height:23px;background:linear-gradient(#c23d14,var(--brick));color:var(--white);font-weight:700;
  font-size:11.3px;letter-spacing:.8px;padding:6px 0 0 12px;border-bottom:2px solid var(--sand-line)}
.topic-list{list-style:none;padding:6px 0 7px 0}
.topic-list li{font-size:10px;color:#4b4b4b;height:17.7px;line-height:17.7px;padding-left:21px;position:relative;letter-spacing:.3px;white-space:nowrap}
.topic-list li::before{content:"";position:absolute;left:9px;top:6px;border-left:4px solid #9a8e70;border-top:3px solid transparent;border-bottom:3px solid transparent}

.section-title{position:absolute;font-family:"Fira Sans",sans-serif;font-size:15px;color:var(--slate);letter-spacing:.5px;font-weight:400}
.welcome-text{position:absolute;left:272px;top:337px;width:360px;font-size:9.7px;line-height:14.5px;color:#444;letter-spacing:.35px}
.office-photo{position:absolute;left:638px;top:341px;width:175px;height:132px;border:3px solid #dcdcd4;
  background:linear-gradient(#9fb6a4 0%,#6d7a5e 40%,#7a5a46 65%,#5d6b44 100%)}
.btn-learn{position:absolute;left:539px;top:453px;width:88px;height:20px;background:linear-gradient(#d84a1c,#b8350f);
  color:var(--white);font-size:9px;font-weight:700;line-height:20px;padding-left:8px;letter-spacing:.3px}
.btn-learn svg{position:absolute;right:8px;top:7px}

.service-list{position:absolute;left:272px;top:528px;list-style:none}
.service-list li{height:17.7px;font-size:9.6px;color:#444;padding-left:18px;position:relative;letter-spacing:.4px;white-space:nowrap}
.service-list svg{position:absolute;left:0;top:-1px}

.offer-box{position:absolute;left:278px;top:713px;width:507px;height:151px;border:2px solid #8e8f86;border-radius:5px;
  background:linear-gradient(#e4e4da,#d3d3c6);overflow:hidden}
.offer-headline{position:absolute;left:11px;top:14px;font-family:"Fira Sans",sans-serif;font-size:16.5px;line-height:29px;color:var(--slate);letter-spacing:1px;z-index:1}
.offer-more{position:absolute;left:243px;top:86px;font-size:10px;color:#5c6a6e;letter-spacing:.6px}
.offer-note{position:absolute;left:0;bottom:0;width:100%;height:35px;background:linear-gradient(90deg,#7e8076,#9a9c90);
  color:var(--white);font-size:9.2px;line-height:14.5px;padding:3px 0 0 7px;letter-spacing:.5px}
.offer-photo{position:absolute;right:0;top:0;width:180px;height:147px;
  background:radial-gradient(ellipse at 40% 50%,#e9b88f 0%,#d8a579 35%,#b7b49d 75%,#cfcfc3 100%)}

.action-btn{position:absolute;left:279px;width:203px;height:34px;border-radius:5px;background:linear-gradient(90deg,#b8350f,#d0481c 55%,#e06a3c);
  color:var(--white);font-family:"Fira Sans",sans-serif;font-size:14.5px;line-height:34px;padding-left:17px;letter-spacing:.6px}
.action-btn svg{position:absolute;right:6px;top:-11px}
.call-box{position:absolute;left:279px;top:1029px;width:203px;height:83px;border-radius:5px;background:var(--sand)}
.call-box .action-btn{position:absolute;left:0;top:0;border-radius:5px 5px 0 0}
.call-text{position:absolute;left:5px;top:40px;font-size:9px;line-height:14.5px;color:#444;letter-spacing:.8px}
.call-text strong{font-weight:700}

.map-frame{position:absolute;left:540px;top:897px;width:245px;height:221px;border:2px solid #cfcfc6;
  background:linear-gradient(135deg,#ecebe5,#dcdbd3)}

.site-footer{position:absolute;left:0;top:1138px;width:886px;height:62px;background:var(--brick)}
.footer-links{position:absolute;left:76px;top:10px;font-size:9.9px;color:var(--white);letter-spacing:.1px}
.copyright{position:absolute;left:76px;top:36px;font-size:9.9px;color:var(--white)}
.to-top{position:absolute;left:732px;top:-3px;width:51px;height:27px;background:#f5f5f5;color:#4f8aa6;font-size:11px;
  text-align:center;line-height:30px}
</style>
</head>
<body>

<header class="site-header">
  <div class="header-band"></div>
  <div class="call-tab">Call for Appointments: (555) 014-2290.</div>
  <h1 class="site-title">Larkmoor Dentist<br>Corwin Hale, DDS, FAGD</h1>
  <div class="hero-photo" role="img" aria-label="Smiling woman with blonde hair"></div>
</header>

<nav class="main-nav">
  <ul>
    <li class="is-current" style="width:62px">Home</li>
    <li style="width:143px">Why we are differnt</li>
    <li style="width:161px">Technologies we offer</li>
    <li style="width:113px">Meet Dr.Hale</li>
    <li style="width:87px">Our Staff</li>
    <li style="width:99px">Contact Us</li>
    <li style="width:74px">Links</li>
  </ul>
</nav>

<aside class="topic-index" aria-label="Dental topics">
  <div class="topic-head">EDUCATION</div>
  <ul class="topic-list">
    <li>Emergency Dental Care</li><li>Your Mouth</li><li>Your Tooth</li><li>Cracked Tooth?</li>
    <li>Missing a Tooth?</li><li>Sensitive Teeth</li><li>Dry MouthTooth</li><li>GrindingSleep</li>
    <li>Dentistry</li><li>Videos</li>
  </ul>
  <div class="topic-head">PREVENTATIVE</div>
  <ul class="topic-list">
    <li>What is Preventive Care?</li><li>Taking Care of Your Teeth</li><li>Eating Right</li>
    <li>Dental Check-Ups Sealants</li><li>Periodontal Disease</li><li>Kicking the Habit</li>
    <li>Night Guards</li><li>Dental X-Rays</li><li>Antibiotics with Treatment</li>
  </ul>
  <div class="topic-head">COSMETICS</div>
  <ul class="topic-list">
    <li>Cosmetic Dentistry</li><li>Bleaching and Whitening</li><li>Cosmetic Bonding</li>
    <li>Esthetic Veneers</li><li>Tooth Shaping</li>
  </ul>
  <div class="topic-head">RESTORATIONS</div>
  <ul class="topic-list">
    <li>Crowns/Caps: Each Step</li><li>CMBRs</li><li>Porcelain Bridges</li><li>Bonded Dental Bridges</li>
    <li>Gold Restorations Implants</li><li>Treating CrackedTeeth</li><li>Periodontal (gum) Treatment</li>
  </ul>
  <div class="topic-head">VISITING OUR OFFICE</div>
  <ul class="topic-list">
    <li>Where to Stay</li><li>First Visit / Map</li><li>Financial Policy</li><li>Dental Insurance</li>
  </ul>
</aside>

<main>
  <h2 class="section-title" style="left:273px;top:310px">Welcome</h2>
  <p class="welcome-text">Lorem ipsum dolor sit amet, consectetuer adipiscing elit. Aenean commodo ligula eget dolor. Aenean massa. Cum sociis natoque penatibus et magnis dis parturient montes, nascetur ridiculus mus. Doneuam felis, ultricies nec, pellentesque eu, pretium quis, sem. Nulla consequat massa quis enim. Donec pede justo, fringilla vel, aliquet nec, vulputate eget, arcu. In enim justo, rhoncus ut, imperdiet a, venenatis vitae, justo.massa quis enim. Donec pede justo,&nbsp; pretium quis, sem. Nulla consequat massa quis enim. Donec pede justo, fringilla vel,</p>
  <div class="office-photo" role="img" aria-label="Stone-faced dental office building among trees"></div>
  <a class="btn-learn">Learn more
    <svg width="10" height="7" viewBox="0 0 10 7"><path d="M0 0l4 3.5L0 7zM5 0l4 3.5L5 7z" fill="#fff"/></svg>
  </a>

  <h2 class="section-title" style="left:274px;top:499px">Dr. Hale Provides</h2>
  <ul class="service-list">
    <li><svg width="12" height="11" viewBox="0 0 12 11"><path d="M1 6l3 4 7-9" fill="none" stroke="#c4371a" stroke-width="2.2"/></svg>General dentistry—oral hygiene, cavity detection and repair, crowns.</li>
    <li><svg width="12" height="11" viewBox="0 0 12 11"><path d="M1 6l3 4 7-9" fill="none" stroke="#c4371a" stroke-width="2.2"/></svg>Cosmetic/restorative dentistry—broken or misshapen teeth, crooked smiles, unsightly gaps</li>
    <li><svg width="12" height="11" viewBox="0 0 12 11"><path d="M1 6l3 4 7-9" fill="none" stroke="#c4371a" stroke-width="2.2"/></svg>Non-metal fillings—nontoxic, durable tooth-colored resin fillings that are proven to provide better results</li>
    <li><svg width="12" height="11" viewBox="0 0 12 11"><path d="M1 6l3 4 7-9" fill="none" stroke="#c4371a" stroke-width="2.2"/></svg>Tooth shaping—extending, shortening or otherwise reshaping teeth for improved esthetics</li>
    <li><svg width="12" height="11" viewBox="0 0 12 11"><path d="M1 6l3 4 7-9" fill="none" stroke="#c4371a" stroke-width="2.2"/></svg>Complete smile make-over's—resin veneers that reshape the whole mouth while preserving natural teeth</li>
    <li><svg width="12" height="11" viewBox="0 0 12 11"><path d="M1 6l3 4 7-9" fill="none" stroke="#c4371a" stroke-width="2.2"/></svg>Tooth whitening—at-home bleaching options to make teeth appear years younger</li>
    <li><svg width="12" height="11" viewBox="0 0 12 11"><path d="M1 6l3 4 7-9" fill="none" stroke="#c4371a" stroke-width="2.2"/></svg>Laser Dentistry, Sleep Dentistry, and Implant Dentistry with the Finest and Latest Equipment and Materials.</li>
    <li><svg width="12" height="11" viewBox="0 0 12 11"><path d="M1 6l3 4 7-9" fill="none" stroke="#c4371a" stroke-width="2.2"/></svg>Dental Implants to replace missing teeth.</li>
    <li><svg width="12" height="11" viewBox="0 0 12 11"><path d="M1 6l3 4 7-9" fill="none" stroke="#c4371a" stroke-width="2.2"/></svg>Sedation Dentistry so you can be relaxed.</li>
  </ul>

  <section class="offer-box">
    <div class="offer-photo" role="img" aria-label="Happy young couple laughing outdoors"></div>
    <p class="offer-headline">We offer an Initial Patient Examination<br>X-rays and Cleaning for $79.00.</p>
    <a class="offer-more">Learn More</a>
    <p class="offer-note">New patients only. Offers are cash patients only.<br>Insurance will be billed at full value.</p>
  </section>

  <a class="action-btn" style="top:896px">Office Hours
    <svg width="44" height="44" viewBox="0 0 44 44"><circle cx="22" cy="22" r="19" fill="#f3b21a"/><circle cx="22" cy="22" r="15" fill="#fff"/><path d="M22 11v11h7" fill="none" stroke="#555" stroke-width="2"/></svg>
  </a>
  <a class="action-btn" style="top:961px">Where to stay?
    <svg width="44" height="44" viewBox="0 0 44 44"><circle cx="22" cy="22" r="19" fill="#fff"/><circle cx="22" cy="22" r="16" fill="#1f6fc9"/><text x="22" y="29" text-anchor="middle" font-family="Arimo,sans-serif" font-weight="700" font-size="20" fill="#fff">?</text></svg>
  </a>
  <div class="call-box">
    <a class="action-btn">Please call
      <svg width="44" height="44" viewBox="0 0 44 44"><path d="M30 4c6 3 8 12 2 22-5 8-12 11-18 10l-3-5 7-4 3 3c4-2 7-7 7-12l-4-1 1-8z" fill="#d8271a"/></svg>
    </a>
    <p class="call-text">contact us outside office hours for an<br>emergency, please call at<br><strong>(555) 018-4471.</strong></p>
  </div>

  <h2 class="section-title" style="left:543px;top:874px">Map to Office</h2>
  <div class="map-frame" role="img" aria-label="Street map showing the route to the dental office"></div>
</main>

<footer class="site-footer">
  <p class="footer-links">Larkmoor Dentist • Tell A Friend • Privacy &amp; Legal • Dental Resources • New Patient Forms</p>
  <p class="copyright">Copyright © 2009. All Rights Reserved</p>
  <a class="to-top">Top</a>
</footer>

</body>
</html>
```